First Aid Kit needs packaging design

We're looking for packaging design for our new first aid kit product. We have the logo created for the product. Our brand name is Oakline Haven and our logo will be provided during the design process. We'll also provide photos (have high res files files for final design), and a template design to base off what we're looking for (packaging design template is .ai file). Logo file also attached (.psd & .png). We need to have the first aid kit contents listed on the back of the packaging (similar to the provided packaging template).

Color: We would like to see black, red, and white throughout the design (similar to provided design template)

The final design should communicate urgency, safety, and portability.

Final design should also include a FNSKU barcode (attached)

Below are more details that define the product.

Product Name:
Ultra-Portable & Small 100-Piece First Aid Kit w/ Exclusive Items, Light, Durable Nylon Case, Space Saving Design - A Must Have Survival Kit!

Product Attributes:
BASED ON CUSTOMER FEEDBACK, our newly designed ultra-lightweight and portable kit has been upgraded with BETTER and STRONGER emergency supplies. Stronger scissors and tweezers, more precise compass, sting relief pads, antibacterial ointment and more!
PRODUCED WITH THE HIGHEST QUALITY STANDARDS that only KVB Approved Facilities can meet.
LIGHTWEIGHT, DURABLE & COMPACT. Perfect for an emergency where a oakline haven is necessary to because seconds count!
The ULTIMATE First Aid Kit for Camping, Home, Road Trips, Office, Adventure, School, Workplace, Travel or Sports.

Product Description
Learn How This Ultra-Portable, Light And Rugged First-Aid Kit Can Give You And Your Family The Ultimate Peace Of Mind.
You need to act fast! Quick Action And A Oakline Haven Is Critical In Emergency Situations.

Stay Alert! Our Kit Has Been Redesigned And Bolstered Based On Your Feedback. Weighing Under 1lb. This Is The Lightest First Aid Kit In Its Class! If You Don't Know What To Do, No Problem; We've Included A First Aid Instruction Guide So You Can Administer Aid Correctly.

Take A Look Inside:

Antiseptic cleansing wipes (6 pcs)
Alcohol prep pad (10 pcs)
Butterfly closure strips (6 pcs)
Sterile Gauze Pad (3 pcs)
Extra large adhesive bandage (4 pc)
Adhesive bandages (25 pcs)
Antibacterial Ointment (4 pcs)
Knuckle adhesive bandage (3 pcs)
Fingertip adhesive bandage (3 pcs)
1 disposable cold compress
First aid tape (1 roll)
Cotton tip applicator (10 pcs)
Abdominal pad (1 pc)
Disposable vinyl gloves (2 pc)
Slim rescue howler whistle (1 pc)
Compass (1pc)
Moleskin blister relief (1 pc)
Triangular bandages (1 pc)
Disposable Emergency blanket (1 pc)
1 glow stick
Disposable raincoat (1 pc)
Scissors (1 pc)
PBT conforming bandage 5x3.6cm (1 roll)
CPR facemask (1 pc)
Metal tweezers (1 pc)
Razor Blade (1 pc)
Sewing Kit (1 pc)
Safety Pins (4 pc)
Sting Relief Pads (4 pc)

Let us know if there are any questions around this.

Thank you,

Milo

Target Market(s)

Health Care, First Aid, Sports & Outdoors, automotive safety, office safety

Industry/Entity Type

Health Care

Font styles to use
Sans Serif
Other font styles liked:
• similar to included box design frame/template

Colors
ec1f27
ffffff
000000

Requirements
Must have
• See Project Description
• Color: Black, red, and white
• Barcode: FNSKU Barcode attached
• Design on back needs to show included contents (similar to design template attached)
Nice to have
• See Project Description

```html
<!DOCTYPE html>
<html lang="en">
<head>
<meta charset="utf-8">
<title>Oakline Haven First Aid Kit – Box Dieline</title>
<link href="https://fonts.googleapis.com/css2?family=Oswald:wght@400;500&family=Roboto+Condensed:wght@400;700&display=swap" rel="stylesheet">
<style>
  :root {
    --red: #ec1f27;
    --red-dark: #c8161d;
    --white: #ffffff;
    --black: #000000;
    --ink: #222222;
    --panel: #2e2e2e;
    --panel-edge: #3b3b3b;
    --stage: #e6e6e6;
    --photo-a: #5d6b4a;
    --photo-b: #8a6f5c;
    --photo-c: #3d4a30;
    --cert: #b9b9b9;
  }
  * { box-sizing: border-box; margin: 0; padding: 0; }
  html, body { width: 1200px; height: 490px; overflow: hidden; background: var(--stage); }
  .dieline { position: relative; width: 1200px; height: 490px; font-family: "Roboto Condensed", Arial, sans-serif; color: var(--white); }
  .abs { position: absolute; }

  .body-band { left: 26px; top: 142px; width: 1104px; height: 322px; background: var(--panel); }
  .end-tab { left: 1130px; top: 142px; }

  .photo { background: linear-gradient(135deg, var(--photo-b) 0%, var(--photo-a) 45%, var(--photo-c) 100%); }
  .photo--front { left: 148px; top: 160px; width: 432px; height: 286px; }
  .photo--back { left: 702px; top: 160px; width: 428px; height: 286px; }

  /* Side panels */
  .side-panel { top: 142px; width: 122px; height: 322px; background: var(--panel); }
  .side-panel--left { left: 26px; }
  .side-panel--right { left: 578px; }
  .corner-cross { left: 0; top: 0; }
  .side-title { left: 14px; top: 22px; font-family: "Oswald", sans-serif; font-weight: 500; font-size: 29px; line-height: 1; white-space: nowrap; letter-spacing: -0.3px; }
  .side-sub { left: 24px; top: 56px; font-family: "Oswald", sans-serif; font-size: 11.5px; line-height: 1; white-space: nowrap; }
  .side-copy { left: 13px; top: 76px; width: 104px; font-size: 6.7px; line-height: 8.6px; font-weight: 700; text-align: justify; }
  .side-copy p + p { margin-top: 8px; }
  .survival-title { left: 13px; top: 226px; font-family: "Oswald", sans-serif; font-weight: 400; font-size: 9.6px; line-height: 1; white-space: nowrap; }
  .use-grid { left: 13px; top: 244px; width: 104px; display: grid; grid-template-columns: 51px 53px; row-gap: 6px; font-family: "Oswald", sans-serif; font-size: 7px; line-height: 11px; }
  .use-grid span { display: flex; align-items: center; gap: 5px; white-space: nowrap; }
  .use-grid i { width: 11px; height: 11px; border: 1px solid var(--white); border-radius: 1px; display: inline-block; flex: none; }

  /* Front panel */
  .red-bar { left: 148px; top: 248px; width: 432px; height: 110px; background: var(--red); }
  .front-cross-v { left: 308px; top: 142px; width: 114px; height: 322px; background: var(--red); }
  .top-flap { left: 308px; top: 28px; width: 114px; height: 114px; background: var(--red); box-shadow: inset 0 -2px 0 var(--red-dark); }
  .flap-title { font-family: "Oswald", sans-serif; font-weight: 500; font-size: 19px; line-height: 1; white-space: nowrap; }
  .flap-sub { font-family: "Oswald", sans-serif; font-size: 7px; line-height: 1; margin-left: 10px; margin-top: 2px; white-space: nowrap; }
  .flap-brand { left: 332px; top: 70px; }
  .flap-brand-back { left: 886px; top: 82px; }
  .flap-cross { position: absolute; left: -14px; top: -10px; }

  .hero-badge { left: 214px; top: 214px; }
  .hero-title { left: 266px; top: 258px; font-family: "Oswald", sans-serif; font-weight: 500; font-size: 54px; line-height: 1; white-space: nowrap; }
  .hero-sub { left: 293px; top: 320px; font-family: "Oswald", sans-serif; font-size: 19px; line-height: 1; white-space: nowrap; }

  .bag-photo { background: linear-gradient(160deg, var(--red) 0%, var(--red-dark) 60%, var(--black) 100%); border-radius: 10px 10px 6px 6px; }
  .bag-photo--front { left: 166px; top: 300px; width: 98px; height: 124px; }
  .bag-photo--back { left: 790px; top: 320px; width: 66px; height: 80px; }

  .tag { background: var(--red); font-family: "Oswald", sans-serif; font-size: 11px; line-height: 15px; padding: 0 5px; white-space: nowrap; }
  .tag--pieces { left: 240px; top: 406px; }
  .tag--weight { left: 204px; top: 424px; }

  .feature-list { left: 308px; top: 374px; width: 114px; list-style: none; font-family: "Oswald", sans-serif; font-size: 9px; text-align: center; }
  .feature-list li { line-height: 15.4px; border-bottom: 1px solid rgba(255,255,255,0.35); white-space: nowrap; }
  .feature-list li:last-child { border-bottom: none; }

  .brand-seal { display: flex; align-items: center; gap: 3px; font-size: 7px; font-weight: 700; color: var(--white); white-space: nowrap; }
  .brand-seal b { width: 14px; height: 14px; border-radius: 50%; background: var(--white); display: inline-block; }
  .brand-seal--front { left: 510px; top: 402px; }
  .brand-seal--back { left: 1062px; top: 402px; }

  /* Back panel */
  .back-red { left: 702px; top: 246px; width: 156px; height: 150px; background: var(--red); }
  .back-copy { left: 709px; top: 258px; width: 144px; font-size: 6.2px; line-height: 8px; font-weight: 700; text-align: justify; }
  .back-copy p + p { margin-top: 7px; width: 78px; }
  .back-badge { left: 822px; top: 300px; }

  .cert-strip { left: 720px; top: 424px; width: 126px; height: 40px; background: var(--white); display: flex; align-items: center; justify-content: space-around; padding: 0 6px; }
  .cert-strip i { width: 20px; height: 20px; border-radius: 50%; background: var(--cert); display: block; }
  .cert-strip i:nth-child(2) { border-radius: 2px; }

  .back-flap { left: 858px; top: 28px; }
  .back-cross-v { left: 858px; top: 142px; width: 116px; height: 322px; background: var(--red); }
  .contents { left: 862px; top: 152px; width: 108px; text-align: right; }
  .contents h2 { font-family: "Oswald", sans-serif; font-weight: 500; font-size: 12px; line-height: 14px; margin-bottom: 2px; white-space: nowrap; }
  .contents ul { list-style: none; font-size: 6.4px; font-weight: 700; line-height: 8.8px; white-space: nowrap; }

  .icon-grid { left: 980px; top: 254px; display: grid; grid-template-columns: repeat(4, 20px); gap: 5px; }
  .icon-grid i { width: 20px; height: 20px; border: 1px solid var(--white); border-radius: 2px; display: block; }

  .label-area { left: 1084px; top: 248px; width: 44px; height: 108px; background: var(--white); }
  .label-text { left: 1112px; top: 250px; width: 104px; transform-origin: 0 0; transform: rotate(90deg) translateY(-12px); font-size: 4.6px; line-height: 5.6px; color: var(--ink); white-space: nowrap; }
</style>
</head>
<body>
<main class="dieline">
  <div class="abs body-band"></div>
  <svg class="abs end-tab" width="24" height="322" viewBox="0 0 24 322" aria-hidden="true">
    <polygon points="0,0 22,14 22,308 0,322" fill="#3b3b3b"/>
  </svg>

  <div class="abs photo photo--front" role="img" aria-label="Photo of a hiker treating a minor injury on a forest trail"></div>
  <div class="abs photo photo--back" role="img" aria-label="Photo of a hiker treating a minor injury on a forest trail"></div>

  <!-- Left side panel -->
  <section class="abs side-panel side-panel--left">
    <svg class="abs corner-cross" width="20" height="30" viewBox="0 0 20 30" aria-hidden="true">
      <rect width="20" height="30" fill="#ec1f27"/>
      <rect x="5" y="8" width="4" height="12" fill="#fff"/><rect x="1" y="12" width="12" height="4" fill="#fff"/>
    </svg>
    <h2 class="abs side-title">FIRST AID</h2>
    <div class="abs side-sub">THE ULTIMATE KIT</div>
    <div class="abs side-copy">
      <p>BASED ON CUSTOMER FEEDBACK, our newly designed ultra-lightweight and portable kit has been upgraded with BETTER and STRONGER emergency supplies. Stronger scissors and tweezers, more precise compass, sting relief pads, antibacterial ointment and more!</p>
      <p>PRODUCED WITH THE HIGHEST QUALITY STANDARDS that only KVB Approved Facilities can meet.</p>
      <p>LIGHTWEIGHT, DURABLE &amp; COMPACT. Perfect for an emergency where a oakline haven is necessary to because seconds count!</p>
    </div>
    <h3 class="abs survival-title">A MUST HAVE SURVIVAL KIT:</h3>
    <div class="abs use-grid">
      <span><i></i>OFFICE</span><span><i></i>CAMPING</span>
      <span><i></i>HOME</span><span><i></i>OUTDOORS</span>
      <span><i></i>TRAVEL</span><span><i></i>SPORTS</span>
      <span><i></i>GENERAL</span><span><i></i>VEHICHLES</span>
    </div>
  </section>

  <!-- Front panel -->
  <div class="abs red-bar"></div>
  <div class="abs front-cross-v"></div>
  <div class="abs top-flap"></div>
  <div class="abs flap-brand">
    <svg class="flap-cross" width="16" height="16" viewBox="0 0 16 16" aria-hidden="true">
      <rect x="5" y="0" width="6" height="16" fill="#fff"/><rect x="0" y="5" width="16" height="6" fill="#fff"/>
    </svg>
    <div class="flap-title">FIRST AID</div>
    <div class="flap-sub">THE ULTIMATE KIT</div>
  </div>
  <svg class="abs hero-badge" width="64" height="64" viewBox="0 0 64 64" aria-hidden="true">
    <circle cx="32" cy="32" r="31" fill="#ec1f27"/>
    <rect x="26" y="15" width="12" height="34" fill="#fff"/><rect x="15" y="26" width="34" height="12" fill="#fff"/>
  </svg>
  <h1 class="abs hero-title">FIRST AID</h1>
  <div class="abs hero-sub">THE ULTIMATE KIT</div>
  <div class="abs bag-photo bag-photo--front" role="img" aria-label="Product photo of the red and black nylon first aid bag"></div>
  <div class="abs tag tag--pieces">100 PIECES</div>
  <div class="abs tag tag--weight">WEIGHT UNDER 1LB</div>
  <ul class="abs feature-list">
    <li>UPGRADED SUPPLIES</li>
    <li>DURABLE NYLON CASE</li>
    <li>LIGHT AND COMPACT</li>
    <li>THE ULTIMATE KIT</li>
  </ul>
  <div class="abs brand-seal brand-seal--front"><b></b>Oakline Haven</div>

  <!-- Right side panel -->
  <section class="abs side-panel side-panel--right">
    <svg class="abs corner-cross" width="20" height="30" viewBox="0 0 20 30" aria-hidden="true">
      <rect width="20" height="30" fill="#ec1f27"/>
      <rect x="5" y="8" width="4" height="12" fill="#fff"/><rect x="1" y="12" width="12" height="4" fill="#fff"/>
    </svg>
    <h2 class="abs side-title">FIRST AID</h2>
    <div class="abs side-sub">THE ULTIMATE KIT</div>
    <div class="abs side-copy">
      <p>BASED ON CUSTOMER FEEDBACK, our newly designed ultra-lightweight and portable kit has been upgraded with BETTER and STRONGER emergency supplies. Stronger scissors and tweezers, more precise compass, sting relief pads, antibacterial ointment and more!</p>
      <p>PRODUCED WITH THE HIGHEST QUALITY STANDARDS that only KVB Approved Facilities can meet.</p>
      <p>LIGHTWEIGHT, DURABLE &amp; COMPACT. Perfect for an emergency where a oakline haven is necessary to because seconds count!</p>
    </div>
    <h3 class="abs survival-title">A MUST HAVE SURVIVAL KIT:</h3>
    <div class="abs use-grid">
      <span><i></i>OFFICE</span><span><i></i>CAMPING</span>
      <span><i></i>HOME</span><span><i></i>OUTDOORS</span>
      <span><i></i>TRAVEL</span><span><i></i>SPORTS</span>
      <span><i></i>GENERAL</span><span><i></i>VEHICHLES</span>
    </div>
  </section>

  <!-- Back panel -->
  <div class="abs back-red"></div>
  <svg class="abs back-badge" width="44" height="44" viewBox="0 0 44 44" aria-hidden="true">
    <circle cx="22" cy="22" r="21" fill="#ec1f27"/>
    <rect x="18" y="10" width="8" height="24" fill="#fff"/><rect x="10" y="18" width="24" height="8" fill="#fff"/>
  </svg>
  <div class="abs back-copy">
    <p>Stay Alert! Our Kit Has Been Redesigned And Bolstered Based On Your Feedback. Weighing Under 1lb. This Is The Lightest First Aid Kit In Its Class! If You Don't Know What To Do, No Problem; We've Included A First Aid Instruction Guide So You Can Administer Aid Correctly.</p>
    <p>Learn How This Ultra-Portable, Light And Rugged First-Aid Kit Can Give You And Your Family The Ultimate Peace Of Mind. You need to act fast! Quick Action And A Oakline Haven Is Critical In Emergency Situations.</p>
  </div>
  <div class="abs bag-photo bag-photo--back" role="img" aria-label="Product photo of the red and black nylon first aid bag"></div>
  <div class="abs cert-strip" aria-label="Quality certification marks"><i></i><i></i><i></i><i></i></div>

  <svg class="abs back-flap" width="116" height="114" viewBox="0 0 116 114" aria-hidden="true">
    <polygon points="0,22 26,22 26,6 32,0 84,0 90,6 90,22 116,22 116,114 0,114" fill="#ec1f27"/>
  </svg>
  <div class="abs flap-brand-back">
    <svg class="flap-cross" width="16" height="16" viewBox="0 0 16 16" aria-hidden="true">
      <rect x="5" y="0" width="6" height="16" fill="#fff"/><rect x="0" y="5" width="16" height="6" fill="#fff"/>
    </svg>
    <div class="flap-title">FIRST AID</div>
    <div class="flap-sub">THE ULTIMATE KIT</div>
  </div>
  <div class="abs back-cross-v"></div>
  <section class="abs contents">
    <h2>TAKE A LOOK INSIDE:</h2>
    <ul>
      <li>Antiseptic cleansing wipes (6 pcs)</li>
      <li>Alcohol prep pad (10 pcs)</li>
      <li>Butterfly closure strips (6 pcs)</li>
      <li>Sterile Gauze Pad (3 pcs)</li>
      <li>Extra large adhesive bandage (4 pc)</li>
      <li>Adhesive bandages (25 pcs)</li>
      <li>Antibacterial Ointment (4 pcs)</li>
      <li>Knuckle adhesive bandage (3 pcs)</li>
      <li>Fingertip adhesive bandage (3 pcs)</li>
      <li>1 disposable cold</li>
      <li>compress First aid tape (1 roll)</li>
      <li>Cotton tip applicator (10 pcs)</li>
      <li>Abdominal pad (1 pc)</li>
      <li>Disposable vinyl gloves (2 pc)</li>
      <li>Slim rescue howler whistle (1 pc)</li>
      <li>Compass (1pc)</li>
      <li>Moleskin blister relief (1 pc)</li>
      <li>Triangular bandages (1 pc)</li>
      <li>Disposable Emergency blanket (1 pc)</li>
      <li>glow stick</li>
      <li>Disposable raincoat (1 pc)</li>
      <li>Scissors (1 pc)</li>
      <li>PBT conf. bandage 5x3.6cm (1 roll)</li>
      <li>CPR facemask (1 pc)</li>
      <li>Metal tweezers (1 pc)</li>
      <li>Razor Blade (1 pc)</li>
      <li>Sewing Kit (1 pc)</li>
      <li>Safety Pins (4 pc)</li>
      <li>Sting Relief Pads (4 pc)</li>
    </ul>
  </section>
  <div class="abs icon-grid" aria-hidden="true">
    <i></i><i></i><i></i><i></i>
    <i></i><i></i><i></i><i></i>
    <i></i><i></i><i></i><i></i>
    <i></i><i></i><i></i><i></i>
  </div>
  <div class="abs label-area" aria-label="FNSKU label area"></div>
  <div class="abs label-text">Ultra-Portable &amp; Small 100-...<br>A Must Have Survival Kit!</div>
  <div class="abs brand-seal brand-seal--back"><b></b>Oakline Haven</div>
</main>
</body>
</html>
```